Thornvale Group needs a business card design

We need a new business card design using the logo recently selected in a logo competition on Pixel Bazaar. Our business is a consultancy specializing in aviation and energy and the winning business card design will promote an image of precision and professionalism with creativity.

Please use the logo with the name on the front of the card and use a complementary font. Make the back white with either the light grey or dark grey logo.

Target Market(s)

Senior finance and legal leaders at aviation and energy companies

Industry/Entity Type

Management Consulting

Contact Information for Business Card

Peter Castrell
President
Thornvale Group

www.thornvalegroup.example

(555) 204-6391
pc@thornvalegroup.example

Requirements
Must have
• Professional font that goes well with the logo font

```html
<!DOCTYPE html>
<html lang="en">
<head>
<meta charset="utf-8">
<title>Thornvale Group – Business Card</title>
<link rel="stylesheet" href="https://fonts.googleapis.com/css2?family=Arimo:wght@400;700&display=swap">
<style>
  :root {
    --canvas: #e7e5e1;
    --navy: #0e4375;
    --slate: #5e6166;
    --paper: #ffffff;
    --paper-shade: #dcdcdc;
    --ink-light: #ffffff;
    --ink-grey: #6b6e73;
    --shadow: rgba(0, 0, 0, 0.22);
  }
  * { box-sizing: border-box; margin: 0; padding: 0; }
  html, body {
    width: 1200px; height: 950px; overflow: hidden;
    background: var(--canvas);
  }
  .canvas { position: relative; width: 1200px; height: 950px; }
  .card {
    position: absolute; left: 215px; width: 770px; height: 440px;
    overflow: hidden; box-shadow: 0 10px 28px var(--shadow);
  }
  .card--back {
    top: 25px;
    background: linear-gradient(135deg, var(--paper) 35%, var(--paper-shade) 100%);
  }
  .card--front { top: 485px; background: var(--paper); }
  .card__art { position: absolute; inset: 0; width: 100%; height: 100%; }

  /* front: contact panel */
  .contact {
    position: absolute; left: 0; top: 0; width: 480px; height: 440px;
    color: var(--ink-light); font-family: "Arimo", Arial, sans-serif;
  }
  .contact__name { position: absolute; left: 52px; top: 34px; font-size: 27px; font-weight: 700; letter-spacing: 0.3px; white-space: nowrap; }
  .contact__title { position: absolute; left: 52px; top: 68px; font-size: 19px; }
  .contact__company { position: absolute; left: 52px; top: 196px; font-size: 18.5px; line-height: 25px; white-space: nowrap; }
  .contact__list { position: absolute; left: 52px; top: 282px; list-style: none; font-size: 18.5px; line-height: 25px; white-space: nowrap; }
  .contact__list li { display: flex; align-items: center; gap: 9px; }
  .contact__list svg { width: 17px; height: 17px; flex: none; }

  /* front: brand name */
  .brand {
    position: absolute; left: 545px; top: 190px; width: 200px;
    text-align: center; font-family: "Arimo", Arial, sans-serif;
    font-weight: 400; font-size: 24px; line-height: 30px;
    color: var(--navy); white-space: nowrap;
  }

  /* back */
  .back-name {
    position: absolute; left: 0; right: 0; top: 160px; text-align: center;
    font-family: "Arimo", Arial, sans-serif; font-weight: 400;
    color: var(--slate); font-size: 40px; letter-spacing: 1px;
  }
  .back-url {
    position: absolute; left: 0; right: 0; top: 300px; text-align: center;
    font-family: "Arimo", Arial, sans-serif; font-size: 20px; letter-spacing: 3px; color: var(--ink-grey);
  }
</style>
</head>
<body>
<main class="canvas">

  <section class="card card--back" aria-label="Card back">
    <p class="back-name">Thornvale Group</p>
    <p class="back-url">www.thornvalegroup.example</p>
  </section>

  <section class="card card--front" aria-label="Card front">
    <svg class="card__art" viewBox="0 0 770 440" aria-hidden="true">
      <defs>
        <linearGradient id="panelBlue" x1="0" y1="0" x2="1" y2="1">
          <stop offset="0" stop-color="#0f4a80"/>
          <stop offset="1" stop-color="#0a3560"/>
        </linearGradient>
        <linearGradient id="panelWhite" x1="0" y1="0" x2="1" y2="1">
          <stop offset="0.3" stop-color="#ffffff"/>
          <stop offset="1" stop-color="#dedede"/>
        </linearGradient>
      </defs>
      <rect width="770" height="440" fill="url(#panelWhite)"/>
      <polygon class="panel-blue" points="0,0 440,0 505,440 0,440" fill="url(#panelBlue)"/>
      <polygon class="panel-fold" points="440,0 478,0 548,440 505,440" fill="#5e6166"/>
      <polygon class="panel-light" points="478,0 770,0 770,440 548,440" fill="url(#panelWhite)"/>
    </svg>

    <div class="contact">
      <p class="contact__name">Peter Castrell</p>
      <p class="contact__title">President</p>
      <p class="contact__company">Thornvale Group LLC<br>Finance and Strategy Consulting<br>Aviation - Manufacturing - Energy</p>
      <ul class="contact__list">
        <li>
          <svg viewBox="0 0 16 16" aria-hidden="true"><path d="M2 5c0-2 2-3 6-3s6 1 6 3l-2 1-1-2H5L4 6Zm2 2h8l1 6H3Z" fill="#fff"/><circle cx="8" cy="10" r="1.6" fill="#0e4375"/></svg>
          (555) 204-6391
        </li>
        <li>
          <svg viewBox="0 0 16 16" aria-hidden="true"><rect x="1" y="3" width="14" height="10" fill="#fff"/><path d="M1 3l7 6 7-6" fill="none" stroke="#0e4375" stroke-width="1.3"/></svg>
          pc@thornvalegroup.example
        </li>
        <li>
          <svg viewBox="0 0 16 16" aria-hidden="true"><circle cx="8" cy="8" r="7" fill="#fff"/><path d="M1 8h14M8 1c-3 3-3 11 0 14M8 1c3 3 3 11 0 14" fill="none" stroke="#0e4375" stroke-width="1"/></svg>
          thornvalegroup.example
        </li>
      </ul>
    </div>

    <p class="brand">Thornvale Group</p>
  </section>

</main>
</body>
</html>
```